Animal Eye Clinic needs a Business card

We are a new veterinary ophthalmology practice (Ridgeline Pet Vision Care) and we need a business card designed. We only see animal eyes - we are not a regular veterinary clinic. We already have a logo. We are looking for a professional, good looking business card to hand out to our clients. We are looking for something simple but professional and contemporary. Our logo is likely the only picture/graphic that needs to be on the card.
Updates

Contact Information for Business Card

Delia Vossman, BSc, DVM, MSc, DipACVO
Veterinary Ophthalmologist

Phone: 250.418.3927
Email: ridgelinepetvisioncare@mailbox-example.net
Website: ridgelinepetvisioncare-example.net
Address: 1874 Thornbury Rd
Kelowna, BC, V1X 4M9

Colors

Designer to choose colors to be used in the design.

Requirements
Must have
• Our logo (attached)

```html
<!DOCTYPE html>
<html lang="en">
<head>
<meta charset="utf-8">
<title>Ridgeline Pet Vision Care – Business Card</title>
<link rel="stylesheet" href="https://fonts.googleapis.com/css2?family=Lato:wght@400;700;900&display=swap">
<style>
  :root {
    --teal: #1aa2b2;
    --teal-deep: #12909f;
    --teal-light: #4fbcc8;
    --ink: #4a4a4c;
    --grey: #8a8a8c;
    --paper: #ffffff;
    --stage: #e9ecee;
  }
  * { box-sizing: border-box; margin: 0; padding: 0; }
  html, body { width: 1200px; height: 900px; overflow: hidden; }
  body {
    background: var(--stage);
    font-family: "Lato", Arial, sans-serif;
    position: relative;
  }
  .card {
    position: absolute;
    width: 560px;
    height: 320px;
    border-radius: 18px;
    overflow: hidden;
    box-shadow: 0 10px 30px rgba(0,0,0,0.18);
  }

  /* Front card */
  .card--front { left: 70px; top: 90px; }
  .front-pattern {
    position: absolute; inset: 0;
    background: linear-gradient(135deg, var(--teal-deep), var(--teal) 55%, var(--teal-light));
  }
  .front-brand {
    position: absolute;
    left: 0; right: 0; top: 128px;
    display: flex; align-items: center; justify-content: center; gap: 14px;
  }
  .brand-dot {
    width: 30px; height: 30px; border-radius: 50%;
    background: var(--ink);
  }
  .brand-name {
    font-weight: 900;
    font-size: 27px;
    letter-spacing: 0.5px;
    text-transform: uppercase;
    color: var(--ink);
  }
  .front-web {
    position: absolute;
    left: 0; right: 0; bottom: 42px;
    text-align: center;
    font-size: 12px;
    letter-spacing: 2.5px;
    color: var(--ink);
  }

  /* Back card */
  .card--back { left: 570px; top: 480px; background: var(--paper); }
  .back-shapes { position: absolute; inset: 0; }
  .back-brand {
    position: absolute;
    left: 112px; top: 70px;
    display: flex; align-items: center; gap: 12px;
  }
  .back-brand .brand-dot { background: var(--teal); width: 26px; height: 26px; }
  .back-brand .brand-name { color: var(--teal); font-size: 22px; }

  .person {
    position: absolute;
    right: 26px; top: 150px;
    text-align: right;
    color: var(--paper);
  }
  .person__name { font-weight: 900; font-size: 16px; text-transform: uppercase; letter-spacing: 0.3px; }
  .person__cred { font-size: 12px; margin-top: 3px; }
  .person__role { font-weight: 700; font-size: 13px; margin-top: 3px; }

  .contact {
    position: absolute;
    left: 30px; bottom: 26px;
    list-style: none;
    color: var(--paper);
    font-size: 12.5px;
  }
  .contact li { display: flex; align-items: center; gap: 9px; margin-top: 5px; }
  .contact svg { width: 13px; height: 13px; fill: var(--paper); flex: none; }
  .contact__address { font-weight: 700; font-size: 14px; padding-left: 22px; }
</style>
</head>
<body>

  <section class="card card--front">
    <div class="front-pattern" role="img" aria-label="Teal background with a light paw print pattern"></div>
    <div class="front-brand">
      <span class="brand-dot"></span>
      <span class="brand-name">Ridgeline Pet Vision Care</span>
    </div>
    <p class="front-web">www.ridgelinepetvisioncare-example.net</p>
  </section>

  <section class="card card--back">
    <svg class="back-shapes" viewBox="0 0 560 320" width="560" height="320" aria-hidden="true">
      <path d="M0,215 C140,175 330,110 560,92 L560,320 L0,320 Z" fill="var(--teal)"/>
      <path d="M150,210 C250,150 360,118 460,104 C370,122 260,158 156,214 Z" fill="var(--grey)"/>
    </svg>

    <div class="back-brand">
      <span class="brand-dot"></span>
      <span class="brand-name">Ridgeline Pet Vision Care</span>
    </div>

    <div class="person">
      <p class="person__name">Delia Vossman</p>
      <p class="person__cred">BSc, DVM, MSc, DipACVO</p>
      <p class="person__role">Veterinary Ophthalmologist</p>
    </div>

    <ul class="contact">
      <li>
        <svg viewBox="0 0 24 24"><path d="M6.6 10.8a15.1 15.1 0 0 0 6.6 6.6l2.2-2.2a1 1 0 0 1 1-.25 11.4 11.4 0 0 0 3.6.57 1 1 0 0 1 1 1V20a1 1 0 0 1-1 1A17 17 0 0 1 3 4a1 1 0 0 1 1-1h3.5a1 1 0 0 1 1 1c0 1.25.2 2.45.57 3.57a1 1 0 0 1-.25 1z"/></svg>
        250.418.3927
      </li>
      <li>
        <svg viewBox="0 0 24 24"><path d="M2 5h20v14H2z M4 7v.5l8 5 8-5V7l-8 5z" fill-rule="evenodd"/></svg>
        ridgelinepetvisioncare@mailbox-example.net
      </li>
      <li class="contact__address">1874 Thornbury Rd, Kelowna, BC, V1X 4M9</li>
    </ul>
  </section>

</body>
</html>
```